Movie poster for indie thriller/film noir GLASS ORCHARD.

GLASS ORCHARD is a thriller about a gangster who forms an unlikely and dangerous friendship with his adulterous wife's former lover. This is a film noir with a romantic/dramatic edge to it, and is inspired by movies like RUN MALLORY, DUSK TRAIN and THE QUILLMAN. Hero is a heartbroken criminal who's torn how to handle his wife's infidelity - he can't bear to kill or hurt her, but hurting people is all he knows. There are no big stars in the movie, so we don't want a poster showing the character's faces, but are looking more for something with an overall graphic concept. Open to ideas in this regard. Will upload some samples of older films/novels that have the feel to them we're after as well as some stills from the movie for inspiration. We like the idea of playing with light and shadow, but wouldn't go full black-and-white - might be better to rather keep a gritty, 70's texture. Our tag line is "FIND WHAT YOU LOVE. LET IT KILL YOU." Dimensions should be 27x40 - full-size movie poster for printing.
Target Market(s)
Audiences that like thrillers.
Industry/Entity Type
Movie
Colors
Designer to choose colors to be used in the design.
Requirements
Must have
- Placement for a credit block, title and our tagline "FIND WHAT YOU LOVE. LET IT KILL YOU."
Nice to have
- Element of danger/thriller. If possible hint at film's romantic edge.
Should not have
- Faces of our actors unless you find a really cool/interesting way to do it. Our actors aren't famous, so audiences will be more interested in a good graphic concept.

```html
<!DOCTYPE html>
<html lang="en">
<head>
<meta charset="utf-8">
<title>Glass Orchard — Poster</title>
<link rel="stylesheet" href="https://fonts.googleapis.com/css2?family=Paytone+One&family=Oswald:wght@400;500&display=swap">
<style>
  :root {
    --backdrop: #f2f2f0;
    --night: #140b0b;
    --oxblood: #2c1013;
    --amber: #c87933;
    --figure: #fbfaf8;
    --credit: #cdb8a4;
  }
  * { margin: 0; padding: 0; box-sizing: border-box; }
  html, body {
    width: 1027px; height: 1200px; overflow: hidden;
    background: var(--backdrop);
  }
  .poster {
    display: block;
    width: 853px; height: 1200px;
    margin: 0 auto;
  }
  .title { font-family: 'Paytone One', sans-serif; fill: var(--amber); }
  .tagline { font-family: 'Paytone One', sans-serif; fill: var(--oxblood); font-size: 40px; }
  .credits { font-family: 'Oswald', sans-serif; fill: var(--credit); font-size: 14px; }
  .credits .label { font-size: 5px; }
</style>
</head>
<body>
<svg class="poster" viewBox="0 0 867 1220" xmlns="http://www.w3.org/2000/svg">
  <defs>
    <radialGradient id="shadow-tone" cx="0.5" cy="0.5" r="0.5">
      <stop offset="0" stop-color="#1a0709" stop-opacity="0.75"/>
      <stop offset="1" stop-color="#1a0709" stop-opacity="0"/>
    </radialGradient>
  </defs>

  <!-- field -->
  <rect class="field-top" width="867" height="460" fill="var(--night)"/>
  <rect class="field-bottom" y="460" width="867" height="760" fill="var(--amber)"/>
  <polygon class="shadow-band" points="685,460 867,460 867,640 485,1220 0,1220 0,885" fill="var(--oxblood)"/>

  <!-- title -->
  <text class="title" x="30" y="225" font-size="275" textLength="810" lengthAdjust="spacingAndGlyphs">GLASS</text>
  <text class="title" x="65" y="420" font-size="212" textLength="760" lengthAdjust="spacingAndGlyphs">ORCHARD</text>

  <!-- cast shadow and figure -->
  <ellipse class="cast-shadow" cx="550" cy="760" rx="220" ry="190" fill="url(#shadow-tone)" role="img" aria-label="Shadow of a woman cast across the dark band"/>
  <rect class="figure" x="75" y="378" width="350" height="587" rx="40" fill="var(--figure)" role="img" aria-label="White silhouette of a man in a suit holding a pistol raised"/>

  <!-- tagline, set along the amber edge of the shadow band -->
  <g class="tagline" transform="translate(540,1206) rotate(-56.6)">
    <text x="0" y="0" textLength="550" lengthAdjust="spacingAndGlyphs">FIND WHAT YOU LOVE,</text>
    <text x="70" y="42" textLength="420" lengthAdjust="spacingAndGlyphs">LET IT KILL YOU.</text>
  </g>

  <!-- credit block -->
  <g class="credits">
    <text x="18" y="1142" textLength="415" lengthAdjust="spacingAndGlyphs">STUDIO NAME PICTURES <tspan class="label">presents a</tspan> PRODUCERS <tspan class="label">a film by</tspan> SCRIPT WRITER ACTOR ONE ACTOR TWO “MOVIE TITLE”</text>
    <text x="18" y="1163" textLength="457" lengthAdjust="spacingAndGlyphs"><tspan class="label">music by</tspan> THE MUSICIAN <tspan class="label">costume designer</tspan> DESIGNER NAME <tspan class="label">edited by</tspan> EDITORS NAME <tspan class="label">production designer</tspan> DESIGNERS NAME <tspan class="label">director of photography</tspan> CINEMATOGRAPHER</text>
    <text x="18" y="1184" textLength="377" lengthAdjust="spacingAndGlyphs"><tspan class="label">executive producer</tspan> EX PRODUCER 1 EX PRODUCER 2 <tspan class="label">produced by</tspan> PRODUCER ONE PRODUCER 2 <tspan class="label">story by</tspan> STORY WRITER</text>
    <text x="18" y="1205" textLength="189" lengthAdjust="spacingAndGlyphs"><tspan class="label">screenplay by</tspan> SCREEN WRITER <tspan class="label">directed by</tspan> DIRECTOR NAME</text>
  </g>
</svg>
</body>
</html>
```